Heron Loan Partners Business Card

We need a business card design for our mortgage servicing company. In addition to servicing the loans of homeowners, we help homeowners with purchasing their homes and any mortgage refinancing. We would like to see designs that use the colors in the logo attached below (gold-ish yellow and navy blue), and any other design you deem fit! The design should communicate a simpler life with smart mortgages provided by Heron.

```html
<!DOCTYPE html>
<html lang="en">
<head>
<meta charset="utf-8">
<title>Heron Loan Partners Business Card</title>
<link href="https://fonts.googleapis.com/css2?family=Open+Sans:wght@400;600;700&display=swap" rel="stylesheet">
<style>
  :root {
    --stage: #303030;
    --gold: #e0b03c;
    --gold-deep: #c99a2e;
    --navy: #221f5c;
    --ink: #1c1c1c;
    --paper: #ffffff;
    --ghost: #ecebf3;
  }
  * { box-sizing: border-box; margin: 0; padding: 0; }
  html, body {
    width: 1200px; height: 780px; overflow: hidden;
    background: var(--stage);
    font-family: "Open Sans", Arial, sans-serif;
  }
  .stage {
    position: relative; width: 1200px; height: 780px;
    display: flex; align-items: center; justify-content: center; gap: 60px;
  }
  .card {
    position: relative; width: 520px; height: 297px; overflow: hidden;
    box-shadow: 0 10px 28px rgba(0,0,0,.45);
  }
  /* back side */
  .card-back { background: var(--gold); }
  .card-back .pattern {
    position: absolute; inset: 0;
    background: linear-gradient(135deg, #e6b84a 0%, var(--gold) 45%, var(--gold-deep) 100%);
  }
  .card-back .brand {
    position: absolute; right: 48px; bottom: 64px;
    display: flex; align-items: center; gap: 6px;
    color: var(--navy); font-weight: 700; font-size: 15px;
  }
  .brand .mark { width: 8px; height: 8px; border-radius: 50%; background: var(--navy); }
  /* front side */
  .card-front { background: var(--paper); }
  .card-front .ghost-name {
    position: absolute; left: 150px; top: 110px;
    font-weight: 700; font-size: 88px; color: var(--ghost);
    letter-spacing: 2px; white-space: nowrap;
  }
  .identity { position: absolute; left: 40px; top: 112px; }
  .identity .name { font-size: 30px; font-weight: 700; line-height: 1; white-space: nowrap; }
  .name .first { color: var(--gold); }
  .name .last { color: var(--navy); }
  .identity .role { margin-top: 6px; margin-left: 70px; font-size: 15px; font-weight: 600; color: var(--ink); }
  .divider { position: absolute; left: 312px; top: 78px; width: 1.5px; height: 92px; background: var(--navy); }
  .contacts { position: absolute; left: 330px; top: 82px; list-style: none; }
  .contacts li {
    display: flex; align-items: center; gap: 8px;
    font-size: 14px; color: var(--ink); height: 27px; white-space: nowrap;
  }
  .contacts svg { width: 14px; height: 14px; flex: none; }
  .address {
    position: absolute; left: 0; right: 0; bottom: 42px; text-align: center;
    font-size: 14px; color: var(--ink); letter-spacing: .3px;
  }
</style>
</head>
<body>
<main class="stage">
  <section class="card card-back">
    <div class="pattern" role="img" aria-label="Repeating brand pattern in gold tones"></div>
    <div class="brand"><span class="mark"></span>Heron</div>
  </section>

  <section class="card card-front">
    <div class="ghost-name" aria-hidden="true">Heron</div>
    <div class="identity">
      <p class="name"><span class="first">Dana</span> <span class="last">Kovarik</span></p>
      <p class="role">Managing Director</p>
    </div>
    <div class="divider"></div>
    <ul class="contacts">
      <li>
        <svg viewBox="0 0 24 24"><path fill="#e0b03c" d="M6.6 10.8a15 15 0 0 0 6.6 6.6l2.2-2.2c.3-.3.7-.4 1-.2 1.1.4 2.3.6 3.6.6.6 0 1 .4 1 1V20c0 .6-.4 1-1 1A17 17 0 0 1 3 4c0-.6.4-1 1-1h3.5c.6 0 1 .4 1 1 0 1.3.2 2.5.6 3.6.1.3 0 .7-.2 1z"/></svg>
        (817) 555-0148
      </li>
      <li>
        <svg viewBox="0 0 24 24"><rect x="2" y="5" width="20" height="14" rx="2" fill="#e0b03c"/><path d="M3 6l9 7 9-7" fill="none" stroke="#fff" stroke-width="1.8"/></svg>
        info@heronloans.com
      </li>
      <li>
        <svg viewBox="0 0 24 24"><circle cx="12" cy="12" r="10" fill="#e0b03c"/><path d="M2 12h20M12 2c3 3 3 17 0 20M12 2c-3 3-3 17 0 20" fill="none" stroke="#fff" stroke-width="1.4"/></svg>
        www.heronloans.com
      </li>
    </ul>
    <p class="address">1840 Willow Bend Rd. Suite 300 Fort Worth, TX 76102</p>
  </section>
</main>
</body>
</html>
```